Velvet Dice Night Age Verification Landing Page

To create a visually appealing design for the landing page of the adult game "Velvet Dice Night" that confirms the visitor's age.
The design should have a simple and visually appealing look that focuses on two buttons labeled "Yes" and "No". The purpose of the page is to confirm that the visitor is 18 years of age or older before accessing the game's content. Responsive design that works well on desktop and mobile devices. The final output should be delivered in PSD, AI, or Sketch format, along with any necessary images or assets.
I have also attached examples.

```html
<!DOCTYPE html>
<html lang="en">
<head>
<meta charset="UTF-8">
<title>Velvet Dice Night — Age Verification</title>
<link href="https://fonts.googleapis.com/css2?family=Poppins:wght@400;500&display=swap" rel="stylesheet">
<style>
  :root {
    --brand-purple: #b04fa6;
    --panel-bg: rgba(52, 48, 46, 0.82);
    --button-muted: #7a7572;
    --text-light: #ffffff;
    --scene-light: #f7efea;
    --scene-skin: #c99a84;
    --scene-deep: #8a5a4c;
  }
  * { margin: 0; padding: 0; box-sizing: border-box; }
  html, body {
    width: 1200px;
    height: 600px;
    overflow: hidden;
    font-family: "Poppins", sans-serif;
  }
  .age-gate {
    position: relative;
    width: 1200px;
    height: 600px;
  }
  .backdrop-photo {
    position: absolute;
    inset: 0;
    background:
      radial-gradient(ellipse 420px 300px at 180px 120px, var(--scene-light) 0%, rgba(247,239,234,0) 100%),
      radial-gradient(ellipse 500px 320px at 900px 380px, #b07e6c 0%, rgba(176,126,108,0) 100%),
      linear-gradient(120deg, #efe4de 0%, var(--scene-skin) 45%, var(--scene-deep) 75%, #a87364 100%);
  }
  .verify-panel {
    position: absolute;
    left: 435px;
    top: 221px;
    width: 365px;
    height: 278px;
    background: var(--panel-bg);
    border-radius: 7px;
  }
  .brand-badge {
    position: absolute;
    left: 539px;
    top: 142px;
    width: 152px;
    height: 152px;
    border-radius: 50%;
    background: var(--brand-purple);
    display: flex;
    align-items: center;
    justify-content: center;
    text-align: center;
    padding: 0 18px;
  }
  .brand-name {
    color: var(--text-light);
    font-size: 20px;
    font-weight: 500;
    line-height: 1.2;
  }
  .verify-question {
    position: absolute;
    left: 435px;
    width: 365px;
    top: 314px;
    text-align: center;
    color: var(--text-light);
    font-size: 16px;
    font-weight: 400;
  }
  .choice-button {
    position: absolute;
    left: 557px;
    width: 116px;
    height: 33px;
    border-radius: 6px;
    color: var(--text-light);
    font-size: 15px;
    display: flex;
    align-items: center;
    justify-content: center;
  }
  .choice-yes { top: 354px; background: var(--brand-purple); }
  .choice-no { top: 397px; background: var(--button-muted); }
  .remember-option {
    position: absolute;
    left: 551px;
    top: 443px;
    display: flex;
    align-items: center;
    gap: 8px;
    color: var(--text-light);
    font-size: 15px;
  }
  .remember-box {
    width: 10px;
    height: 10px;
    background: var(--text-light);
  }
</style>
</head>
<body>
  <main class="age-gate">
    <div class="backdrop-photo" role="img" aria-label="Soft-focus photo of an embracing couple on white bed sheets"></div>
    <section class="verify-panel"></section>
    <div class="brand-badge"><span class="brand-name">Velvet Dice Night</span></div>
    <p class="verify-question">Are you over 18 years of age?</p>
    <div class="choice-button choice-yes">Yes</div>
    <div class="choice-button choice-no">No</div>
    <div class="remember-option"><span class="remember-box"></span><span>Remember me</span></div>
  </main>
</body>
</html>
```